Ridge Lass Crew (Flyer)

I want a flyer to advertise my service.
Details below, and logo's to use are attached.

A girls only after school program, 11-14yrs, as OSHC is no longer avail, dedicated to coaching & mentoring our girls into strong, independent young women.

The Brainchild of Rebecca Folwin, Ridge Lass Crew was created to address the growing demand for after school/school holiday supervision for kids moving from primary into high school, when OSHC ceases to exist.
With over 12 years experience mentoring and coaching young women in the corporate world, Bec decided to leave her role as a Director with Tarrant Trust, and follow her passion.
Bec, along with her sister Lorraine, who has over 10 years experience in local communities as a Youth Worker, and is also a qualified Enrolled Nurse, embarked on building a program designed to keep parents happy (by knowing their girls are safe) and dedicated to coaching and mentoring our girls into strong, independent young women.
Open every afternoon and during school holidays, we look to offer;
- Daily meditation
- Healthy snacks
- Dedicated homework time
- Organised group activity, led by qualified instructors (yoga, fitness class, soccer etc)
- Regular guests speakers, addressing issues/concerns for young people today
- SOCIAL MEDIA FREE ZONE

Located 87 Pelham Pde, Brackenvale (across from Crestmoor Day Clinic)
Open 3-6pm Monday to Friday

Facebook page: http://fb.example/ridgelasscrew
Email: info@ridgelasscrew.example.au
Mobile: 0455817396

Target Market(s)

Parents of teenage girls, teenage girls 11-14 years

Industry/Entity Type

School

Font styles to use
Sans Serif

Colors
b768aa
e667a6

Requirements
Must have
• What progam is - see brief
• Who runs it
Should not have
• Not be too busy, not overly mature images

```html
<!DOCTYPE html>
<html lang="en">
<head>
<meta charset="utf-8">
<title>Ridge Lass Crew – After School Program</title>
<link rel="stylesheet" href="https://fonts.googleapis.com/css2?family=Amaranth:wght@400;700&family=Cinzel:wght@400&family=Crimson+Text:ital@1&family=Lora:wght@500&family=Open+Sans:wght@600;700&family=Roboto+Condensed:wght@400&display=swap">
<style>
  :root {
    --pink: #e667a6;
    --pink-page: #e56ea8;
    --purple: #b768aa;
    --lavender: #dab6e1;
    --white: #ffffff;
    --ink: #1a1a1a;
    --slate: #3a3a3a;
    --frame: #d9d9d9;
    --blue-deep: #0d4d8f;
    --blue-mid: #2b7fc4;
    --blue-light: #5aa9e0;
  }
  * { box-sizing: border-box; margin: 0; padding: 0; }
  html, body { width: 927px; height: 1200px; overflow: hidden; background: var(--pink-page); }
  .flyer { position: relative; width: 927px; height: 1200px; background: var(--pink-page); overflow: hidden; }

  .hero-image {
    position: absolute; left: 0; top: 45px; width: 927px; height: 453px;
    background: radial-gradient(ellipse at 60% 40%, var(--blue-light) 0%, var(--blue-mid) 45%, var(--blue-deep) 100%);
  }
  .brand-box {
    position: absolute; left: 50px; top: 6px; width: 274px; height: 328px;
    background: var(--white); display: flex; align-items: center; justify-content: center;
  }
  .brand-name {
    font-family: "Amaranth", sans-serif; font-weight: 700; font-size: 52px; line-height: 1;
    color: var(--pink); text-align: center;
  }

  .photo {
    position: absolute; top: 336px; width: 202px; height: 202px; border-radius: 50%;
    border: 7px solid var(--frame);
  }
  .photo-soccer { left: 144px; background: linear-gradient(160deg, #8fb07a, #4d6b3a 55%, #e0772e); }
  .photo-team { left: 362px; background: linear-gradient(180deg, #3d3a3a, #b92b33 55%, #1e2a4a); }
  .photo-study { left: 579px; background: linear-gradient(160deg, #e9dcc6, #caa58a 50%, #d94b3e); }

  .program-box {
    position: absolute; left: 102px; top: 540px; width: 730px; height: 114px;
    background: var(--purple); border-radius: 8px; color: var(--white); text-align: center;
  }
  .program-title { font-family: "Amaranth", sans-serif; font-weight: 400; font-size: 47px; line-height: 1; padding-top: 6px; }
  .program-ages { margin-top: 4px; margin-left: 116px; text-align: left; font-family: "Open Sans", sans-serif; line-height: 1.1; }
  .program-ages .age { font-size: 46px; font-weight: 700; }
  .program-ages .note { font-size: 24px; font-weight: 600; margin-left: 12px; }

  .founder-box {
    position: absolute; left: 124px; top: 698px; width: 713px; height: 99px;
    background: var(--lavender); text-align: center; color: var(--ink);
    font-family: "Cinzel", serif; font-size: 33px; line-height: 42px; padding-top: 6px; letter-spacing: 2px;
  }

  .offer-heading {
    position: absolute; left: 46px; top: 817px;
    font-family: "Amaranth", sans-serif; font-weight: 400; font-size: 37px; color: var(--white);
    text-shadow: 1px 1px 2px rgba(0,0,0,.35);
  }
  .offer-list { list-style: none; }
  .offer-item {
    position: absolute; display: flex; align-items: center; gap: 14px; white-space: nowrap;
    font-family: "Crimson Text", serif; font-style: italic; font-size: 29px; line-height: 1; color: var(--white); letter-spacing: 1.5px;
  }
  .offer-item svg { width: 17px; height: 17px; flex: none; }

  .hours-heading {
    position: absolute; left: 0; width: 927px; top: 1015px; text-align: center;
    font-family: "Lora", serif; font-weight: 500; font-size: 34px; line-height: 1.1; color: var(--ink);
  }
  .hours-times {
    position: absolute; left: 0; width: 927px; top: 1053px; text-align: center;
    font-family: "Open Sans", sans-serif; font-weight: 700; font-size: 25px; line-height: 1.1; color: var(--slate);
    text-shadow: 1px 1px 1px rgba(0,0,0,.3);
  }

  .contact-bar {
    position: absolute; left: 0; top: 1090px; width: 927px; height: 110px; background: var(--purple);
    font-family: "Roboto Condensed", sans-serif; color: var(--white); font-size: 20px; line-height: 1.35;
  }
  .contact { position: absolute; display: flex; align-items: center; gap: 12px; }
  .contact svg { flex: none; }
  .contact-email { left: 16px; top: 12px; gap: 29px; }
  .contact-social { left: 16px; top: 74px; font-size: 18px; }
  .social-dot { width: 30px; height: 30px; border-radius: 50%; background: var(--white); flex: none; margin-right: 12px; }
  .contact-phone { left: 394px; top: 31px; gap: 13px; }
  .contact-address { left: 678px; top: 28px; gap: 12px; }
  .contact-address small { font-size: 15px; }
</style>
</head>
<body>
<main class="flyer">
  <div class="hero-image" role="img" aria-label="Blue banner photo of a smiling girl with arms outstretched among training and coaching words"></div>

  <div class="brand-box"><span class="brand-name">Ridge<br>Lass<br>Crew</span></div>

  <div class="photo photo-soccer" role="img" aria-label="Photo of a girl heading a soccer ball"></div>
  <div class="photo photo-team" role="img" aria-label="Photo of a girls soccer team huddled with a coach"></div>
  <div class="photo photo-study" role="img" aria-label="Photo of a girl studying in a library"></div>

  <section class="program-box">
    <h1 class="program-title">A Girls Only After School Program</h1>
    <p class="program-ages"><span class="age">11-14yrs</span><span class="note">as OSHC is no longer available</span></p>
  </section>

  <section class="founder-box">
    <p>The Brainchild of Rebecca Folwin</p>
    <p>Ridge Lass Crew</p>
  </section>

  <h2 class="offer-heading">We look to offer</h2>
  <ul class="offer-list">
    <li class="offer-item" style="left:30px;top:875px"><svg viewBox="0 0 20 20"><circle cx="10" cy="10" r="8" fill="none" stroke="#fff" stroke-width="2"/><path d="M6 10.5l3 3 5-6" fill="none" stroke="#fff" stroke-width="2"/></svg>Daily meditation</li>
    <li class="offer-item" style="left:306px;top:877px"><svg viewBox="0 0 20 20"><circle cx="10" cy="10" r="8" fill="none" stroke="#fff" stroke-width="2"/><path d="M6 10.5l3 3 5-6" fill="none" stroke="#fff" stroke-width="2"/></svg>Healthy snacks</li>
    <li class="offer-item" style="left:557px;top:877px"><svg viewBox="0 0 20 20"><circle cx="10" cy="10" r="8" fill="none" stroke="#fff" stroke-width="2"/><path d="M6 10.5l3 3 5-6" fill="none" stroke="#fff" stroke-width="2"/></svg>Dedicated homework time</li>
    <li class="offer-item" style="left:63px;top:921px"><svg viewBox="0 0 20 20"><circle cx="10" cy="10" r="8" fill="none" stroke="#fff" stroke-width="2"/><path d="M6 10.5l3 3 5-6" fill="none" stroke="#fff" stroke-width="2"/></svg>Organised group activity, (yoga, fitness class, soccer etc.)</li>
    <li class="offer-item" style="left:108px;top:967px"><svg viewBox="0 0 20 20"><circle cx="10" cy="10" r="8" fill="none" stroke="#fff" stroke-width="2"/><path d="M6 10.5l3 3 5-6" fill="none" stroke="#fff" stroke-width="2"/></svg>Regular guests speakers</li>
    <li class="offer-item" style="left:458px;top:967px"><svg viewBox="0 0 20 20"><circle cx="10" cy="10" r="8" fill="none" stroke="#fff" stroke-width="2"/><path d="M6 10.5l3 3 5-6" fill="none" stroke="#fff" stroke-width="2"/></svg>Social media free zone</li>
  </ul>

  <p class="hours-heading">Open every afternoon and during school holidays</p>
  <p class="hours-times">3-6pm Monday to Friday</p>

  <footer class="contact-bar">
    <div class="contact contact-email">
      <svg width="30" height="24" viewBox="0 0 32 26"><rect x="1" y="1" width="30" height="24" rx="3" fill="#fff"/><path d="M3 4l13 10 13-10" fill="none" stroke="#b768aa" stroke-width="2.5"/></svg>
      <span>e-Mail us<br>info@ridgelasscrew.example.au</span>
    </div>
    <div class="contact contact-social"><span class="social-dot"></span><span>http://fb.example/ridgelasscrew</span></div>
    <div class="contact contact-phone">
      <svg width="18" height="34" viewBox="0 0 18 34"><rect x="1" y="1" width="16" height="32" rx="3" fill="#fff"/><rect x="4" y="5" width="10" height="20" fill="#b768aa"/><circle cx="9" cy="29" r="1.8" fill="#b768aa"/></svg>
      <span>Call Us Now<br>0455817396</span>
    </div>
    <div class="contact contact-address">
      <svg width="22" height="34" viewBox="0 0 22 34"><path d="M11 1C5 1 1 5.5 1 11c0 8 10 22 10 22s10-14 10-22C21 5.5 17 1 11 1z" fill="#fff"/><circle cx="11" cy="11" r="4" fill="#b768aa"/></svg>
      <span>87 Pelham Pde,<br>Brackenvale<br><small>(across from Crestmoor Day Clinic)</small></span>
    </div>
  </footer>
</main>
</body>
</html>
```